T SHIRT BUSINESS That needs a Flyer of SERVICES offered (LOGO PROVIDED)

I want a flyer created for my Custom Tshirt Design business (CAPS IN BLOOM). I want to be able to hand this to a customer so that they can easily find the info they need about my business to be able to contact me for their custom tshirt needs. I would like to display some of our custom artwork that will entice the buyer to SHOP! This flyer should be colorful and bold but please not clutter. I want it to be very professional looking so that when printed on high quality stock it will be attractive.

Target Market(s)

CUSTOM DESIGN CLOTHING AUDIENCE.

Industry/Entity Type

Clothing

Font styles to use
Decorative

Colors
ec1f27
fbed22
0455a3

Requirements
Must have
• Business Info
Name: CAPS IN BLOOM
NUMBER: 555-271-8390
email: capsinbloom@mailbay.com
website: capsinbloom.com
FB: CAPSINBLOOM
Instagram: @capsinbloom
Business Description: Design Custom Apparel
Type: DTG and Vinyl Printing
SLOGAN: CAPS IN BLOOM - WE KEEP GLOWING!
PRICING: CUSTOM T-SHIRTS STARING @ $25
Nice to have
• Additional inputs from the designer
Should not have
• Please do not make the flyer cluttered.

```html
<!DOCTYPE html>
<html lang="en">
<head>
<meta charset="utf-8">
<title>Caps In Bloom – Custom T-Shirt Flyer</title>
<link rel="stylesheet" href="https://fonts.googleapis.com/css2?family=Oswald:wght@500;600;700&family=Special+Elite&family=Montserrat:wght@600;700;900&display=swap">
<style>
  :root {
    --stage: #2d2d2d;
    --cream: #fbf3d0;
    --cream-glow: #fffbe8;
    --butter: #f6e7a6;
    --red: #ec1f27;
    --red-deep: #c8161d;
    --navy: #1b3a6e;
    --blue: #0455a3;
    --blue-deep: #063f7d;
    --ink: #1d1d1d;
    --paper: #f7f7f5;
    --white: #ffffff;
  }
  * { box-sizing: border-box; margin: 0; padding: 0; }
  html, body { width: 1200px; height: 613px; overflow: hidden; }
  body { background: var(--stage); position: relative; }

  .flyer {
    position: absolute; left: 400px; top: 24px;
    width: 400px; height: 566px; overflow: hidden;
    background: radial-gradient(ellipse at 60% 20%, var(--cream-glow) 0%, var(--cream) 45%, var(--butter) 100%);
    box-shadow: 0 8px 22px rgba(0,0,0,.45);
  }
  .flyer-bands { position: absolute; inset: 0; }

  .brand-mark {
    position: absolute; left: 0; right: 0; top: 58px;
    display: flex; align-items: center; justify-content: center; gap: 6px;
    font-family: "Oswald", sans-serif; font-weight: 600; font-size: 15px;
    letter-spacing: 1px; color: var(--red);
  }
  .brand-dot { width: 12px; height: 12px; border-radius: 50%; background: var(--red); }

  .headline {
    position: absolute; left: 0; right: 0; text-align: center;
    font-family: "Oswald", sans-serif; font-weight: 700; line-height: 1;
    text-transform: uppercase;
  }
  .headline-name { top: 104px; font-size: 46px; color: var(--red-deep); letter-spacing: .5px; }
  .headline-slogan { top: 154px; font-size: 44px; color: var(--navy); letter-spacing: 0; }

  .services {
    position: absolute; left: 32px; right: 36px; top: 212px;
    display: flex; justify-content: space-between; align-items: flex-start;
    font-family: "Special Elite", monospace; font-size: 16px; line-height: 1.2;
  }
  .service-design { color: var(--ink); }
  .service-print { color: var(--red-deep); text-align: right; }
  .service-divider { width: 1px; height: 20px; background: var(--ink); margin-top: 2px; }

  .shirt-showcase {
    position: absolute; left: 24px; top: 302px; width: 352px; height: 150px;
    border-radius: 6px;
    background: linear-gradient(180deg, #2a2a2a 0%, #121212 100%);
  }

  .offer { position: absolute; left: 0; right: 0; top: 458px; text-align: center; }
  .offer-label {
    display: flex; align-items: center; justify-content: center; gap: 8px;
    font-family: "Montserrat", sans-serif; font-weight: 700; font-size: 14px; color: var(--red);
  }
  .offer-label::before, .offer-label::after { content: ""; width: 20px; height: 1.5px; background: var(--ink); }
  .offer-price {
    font-family: "Montserrat", sans-serif; font-weight: 900; font-size: 32px;
    color: var(--ink); line-height: 1.05; letter-spacing: -.5px;
  }
  .offer-price sup { font-size: 18px; vertical-align: 11px; }

  .contact-phone {
    position: absolute; left: 10px; top: 521px;
    display: flex; align-items: center; gap: 4px;
    font-family: "Oswald", sans-serif; font-weight: 600; font-size: 27px; color: var(--white);
  }
  .contact-phone svg { width: 20px; height: 24px; }
  .contact-divider { position: absolute; left: 196px; top: 522px; width: 1.5px; height: 36px; background: var(--white); }
  .contact-list {
    position: absolute; left: 204px; right: 10px; top: 520px; list-style: none;
    font-family: "Montserrat", sans-serif; font-weight: 600; font-size: 9px;
    line-height: 13px; color: var(--white); white-space: nowrap;
  }
  .contact-list li { display: flex; align-items: center; gap: 4px; }
  .contact-dot { width: 7px; height: 7px; border-radius: 50%; background: var(--red); flex: none; }
  .contact-dot.spaced { margin-left: 5px; }
</style>
</head>
<body>
  <main class="flyer">
    <svg class="flyer-bands" viewBox="0 0 400 566" aria-hidden="true">
      <defs>
        <radialGradient id="red-burst" cx="50%" cy="40%" r="70%">
          <stop offset="0" stop-color="#f0343a"/>
          <stop offset="1" stop-color="#c8161d"/>
        </radialGradient>
        <linearGradient id="blue-band" x1="0" y1="0" x2="0" y2="1">
          <stop offset="0" stop-color="#0455a3"/>
          <stop offset="1" stop-color="#063f7d"/>
        </linearGradient>
      </defs>
      <path fill="url(#red-burst)" d="M0 266 L40 262 L80 264 L120 258 L160 257 L200 252 L240 250 L280 252 L320 248 L360 250 L400 247 V460 H0Z"/>
      <path fill="#f7f7f5" d="M0 452 L30 448 L70 451 L110 446 L150 449 L200 444 L250 447 L300 443 L350 446 L400 442 V520 H0Z"/>
      <path fill="url(#blue-band)" d="M0 514 L50 512 L100 514 L150 510 L200 512 L260 508 L320 510 L400 506 V566 H0Z"/>
    </svg>

    <div class="brand-mark"><span class="brand-dot"></span>CAPS IN BLOOM</div>

    <h1 class="headline headline-name">Caps In Bloom</h1>
    <h2 class="headline headline-slogan">We Keep Glowing!</h2>

    <div class="services">
      <p class="service-design">Design Custom<br>Apparel</p>
      <span class="service-divider"></span>
      <p class="service-print">DTG and Vinyl<br>Printing</p>
    </div>

    <div class="shirt-showcase" role="img" aria-label="Three black custom T-shirts on hangers showing printed artwork"></div>

    <div class="offer">
      <p class="offer-label">CUSTOM T-SHIRTS</p>
      <p class="offer-price">STARING @ <sup>$</sup>25</p>
    </div>

    <div class="contact-phone">
      <svg viewBox="0 0 22 26" aria-hidden="true">
        <rect x="5" y="1" width="13" height="22" rx="2.5" fill="#ec1f27"/>
        <rect x="7.5" y="4" width="8" height="14" rx="1" fill="#063f7d"/>
        <circle cx="11.5" cy="20.5" r="1.2" fill="#063f7d"/>
      </svg>
      <span>555-271-8390</span>
    </div>
    <span class="contact-divider"></span>
    <ul class="contact-list">
      <li><span class="contact-dot"></span>capsinbloom@mailbay.com</li>
      <li><span class="contact-dot"></span>www.capsinbloom.com</li>
      <li><span class="contact-dot"></span>CAPSINBLOOM<span class="contact-dot spaced"></span>@capsinbloom</li>
    </ul>
  </main>
</body>
</html>
```